Redesign of Form/Document Navigation Page

I need a redesign of our document and navigation bar on the left. We want the same navigation bar layout/setup but want the buttons and typography to be simple and matching all over. The form needs to be aesthetically pleasing and fit within the page.

1st attachment is our Direct Deposit and the second is the form continued.

```html
<!DOCTYPE html>
<html lang="en">
<head>
<meta charset="utf-8">
<title>Employee Direct Deposit Enrollment Form</title>
<link href="https://fonts.googleapis.com/css2?family=Open+Sans:wght@400;600;700&display=swap" rel="stylesheet">
<style>
:root{
  --navy:#27265f;
  --gold:#e8ae1f;
  --gold-dark:#d99a12;
  --red:#d0342c;
  --panel:#f4f4f4;
  --band:#ebebeb;
  --line:#c9c9c9;
  --text:#333;
  --muted:#666;
  --white:#fff;
}
*{box-sizing:border-box;margin:0;padding:0}
html,body{width:833px;height:1200px;overflow:hidden}
body{font-family:"Open Sans",sans-serif;background:var(--white);color:var(--text);position:relative}
.abs{position:absolute}
.brand{left:92px;top:26px;display:flex;align-items:center;gap:8px}
.brand-mark{width:20px;height:20px;background:var(--navy);border-radius:50%}
.brand-name{font-weight:600;color:var(--navy);font-size:17px;line-height:22px}
.top-links{top:32px;left:574px;font-size:8px;color:#4b4a8a;display:flex;gap:12px}
.user{left:667px;top:24px;display:flex;align-items:center;gap:6px;font-size:8px;color:#222}
.avatar{width:25px;height:25px;border-radius:50%;background:linear-gradient(135deg,#c9a58a,#8a6a55)}
.band{left:0;top:76px;width:833px;height:28px;background:var(--band)}
.back{left:92px;top:76px;width:78px;height:28px;background:var(--navy);color:var(--white);font-size:7.5px;display:flex;align-items:center;justify-content:center}
.nav{left:92px;top:112px;width:166px}
.nav-item{height:55px;margin-bottom:2px;background:var(--navy);color:var(--white);font-size:10.5px;display:flex;align-items:center;padding-left:16px;gap:10px;position:relative}
.nav-item svg{width:18px;height:18px}
.nav-item.active{background:var(--gold)}
.nav-item.active::after{content:"";position:absolute;right:-8px;top:19px;border-left:8px solid var(--gold);border-top:9px solid transparent;border-bottom:9px solid transparent}
.panel{left:261px;top:112px;width:480px;height:1021px;background:var(--panel)}
.title{left:281px;top:128px;font-size:16.5px;font-weight:400;color:var(--red)}
.intro{left:282px;width:438px;font-size:7.3px;line-height:13.4px;color:#333}
.attach{left:283px;top:250px;width:436px;height:78px;border:1px solid var(--line);background:var(--white);text-align:center;padding-top:16px;font-size:9.5px;color:#3b3a78}
.refresh{display:inline-flex;align-items:center;gap:4px;margin-top:6px;border:1px solid #bbb;border-radius:3px;padding:6px 10px;font-size:8px;color:#333;background:var(--white)}
.section{font-size:10px;color:#3b3a78}
.small{font-size:7px;color:#222}
.note{font-size:10px;color:#222}
.warn{font-size:9.5px;color:var(--red)}
.radio{display:inline-flex;align-items:center;gap:4px;font-size:10px;color:#222}
.radio::before{content:"";width:7px;height:7px;border:1px solid #999;border-radius:50%;background:var(--white)}
.label{font-size:10px;color:#222}
.field{height:28px;border:1px solid var(--line);background:var(--white)}
.field.tall{height:34px}
.amount{font-size:8px;color:#999;display:flex;justify-content:space-between;align-items:center;padding:0 10px}
.legal{left:283px;top:661px;width:436px;height:150px;border:1px solid var(--line);background:var(--white);padding:12px 14px}
.legal h2{font-size:10.5px;font-weight:400;color:#3b3a78;margin-bottom:6px}
.legal p{font-size:7px;line-height:13.4px;color:#666;text-align:justify}
.accept{left:282px;top:902px;width:111px;height:34px;background:linear-gradient(var(--gold),var(--gold-dark));border-radius:2px;font-size:10px;font-weight:600;color:#3a2c05;display:flex;align-items:center;justify-content:center}
.footer{left:0;top:1162px;width:833px;height:38px;background:var(--band);font-size:7.5px;color:#333;text-align:center;line-height:38px}
</style>
</head>
<body>
<header>
  <div class="abs brand"><span class="brand-mark"></span><span class="brand-name">Sentinel Shield Services</span></div>
  <nav class="abs top-links"><span>⌂ Home</span><span>⊕ Help</span></nav>
  <div class="abs user"><span class="avatar" role="img" aria-label="User profile photo"></span>Mara Ellis</div>
</header>
<div class="abs band"></div>
<div class="abs back">« Back To Profile</div>

<aside class="abs nav">
  <div class="nav-item active"><svg viewBox="0 0 18 18"><rect x="1" y="4" width="16" height="10" rx="1" fill="none" stroke="#fff" stroke-width="1.5"/><circle cx="9" cy="9" r="2.5" fill="#fff"/></svg>Direct Deposit</div>
  <div class="nav-item"><svg viewBox="0 0 18 18"><path d="M4 1h7l4 4v12H4z" fill="none" stroke="#fff" stroke-width="1.4"/><path d="M6 8h7M6 11h7M6 14h7" stroke="#fff"/></svg>Change W-4</div>
  <div class="nav-item"><svg viewBox="0 0 18 18"><path d="M2 7h6V3l6 6-6 6v-4H2z" fill="#fff"/><path d="M12 2h4v14h-4" fill="none" stroke="#fff" stroke-width="1.4"/></svg>Labour Code</div>
  <div class="nav-item"><svg viewBox="0 0 18 18"><circle cx="9" cy="9" r="8" fill="#fff"/><rect x="8" y="4" width="2" height="6" fill="#27265f"/><rect x="8" y="12" width="2" height="2" fill="#27265f"/></svg>Personal Information</div>
  <div class="nav-item"><svg viewBox="0 0 18 18"><rect x="1" y="4" width="16" height="12" fill="none" stroke="#fff" stroke-width="1.5"/><path d="M6 4V2h6v2" fill="none" stroke="#fff"/><path d="M9 7v6M6 10h6" stroke="#fff" stroke-width="2"/></svg>Appraisal and Review</div>
  <div class="nav-item"><svg viewBox="0 0 18 18"><rect x="2" y="6" width="9" height="11" fill="none" stroke="#fff" stroke-width="1.4"/><path d="M7 6V2h9v11h-5" fill="none" stroke="#fff" stroke-width="1.4"/></svg>Write Up-Slip</div>
  <div class="nav-item"><svg viewBox="0 0 18 18"><path d="M1 1v16h16" fill="none" stroke="#fff" stroke-width="1.4"/><rect x="4" y="9" width="2" height="6" fill="#fff"/><rect x="8" y="6" width="2" height="9" fill="#fff"/><rect x="12" y="4" width="2" height="11" fill="#fff"/></svg>Employee Performance</div>
</aside>

<main>
  <div class="abs panel"></div>
  <h1 class="abs title">Employee Direct Deposit Enrollment Form</h1>
  <p class="abs intro" style="top:157px">To enroll in Direct Deposit, simply fill out this form. Attach a voided check for each checking account - not a deposit slip. If depositing to a savings account, ask your bank to give you the Routing/Transit Number for your account it isn't always the same as the number on a savings deposit slip. This help ensure that you are paid correctly. Once filled out, accounting will review your information for processing. Once processed, you will receive an email confirmation with details.</p>
  <p class="abs intro" style="top:216px">Employees must attach a voided check for each of their accounts to help verify their account numbers and bank routing numbers.</p>

  <div class="abs attach">Attach A Voided Check Or Bank Deposit Form for the Account<br>
    <span class="refresh"><svg width="8" height="8" viewBox="0 0 10 10"><path d="M8 3A4 4 0 1 0 9 6" fill="none" stroke="#333" stroke-width="1.4"/><path d="M9 0v4H5z" fill="#333"/></svg>Refresh</span></div>

  <div class="abs section" style="left:283px;top:351px">Account Information</div>
  <div class="abs small" style="left:282px;top:370px">The last item must be for the remaining amount owed to you. To distribute to more account, please complete another form.</div>
  <div class="abs note" style="left:282px;top:382px">Make sure to indicate what kind of account, along with enrolling or declining</div>
  <div class="abs warn" style="left:282px;top:405px">**NOTIFY PAYROLL IMMEDIATELY IF YOU CLOSE OR CHANGE BANK ACCOUNT**</div>
  <div class="abs" style="left:282px;top:427px;display:flex;gap:20px">
    <span class="radio">New Enrollment</span><span class="radio">Change Enrollment</span><span class="radio">Cancel Enrollment</span>
  </div>

  <div class="abs label" style="left:282px;top:466px">Basic Name</div>
  <div class="abs label" style="left:434px;top:466px">City</div>
  <div class="abs label" style="left:586px;top:466px">State</div>
  <div class="abs field" style="left:282px;top:483px;width:133px"></div>
  <div class="abs field" style="left:434px;top:483px;width:133px"></div>
  <div class="abs field" style="left:586px;top:483px;width:133px"></div>

  <div class="abs label" style="left:282px;top:527px">Routing Transit Number</div>
  <div class="abs label" style="left:434px;top:527px">Account Number</div>
  <div class="abs field" style="left:282px;top:544px;width:133px"></div>
  <div class="abs field" style="left:434px;top:544px;width:133px"></div>

  <div class="abs label" style="left:434px;top:588px">Amount</div>
  <div class="abs" style="left:282px;top:609px;display:flex;gap:32px"><span class="radio">Checking</span><span class="radio">Savings</span></div>
  <div class="abs field amount" style="left:434px;top:604px;width:133px"><span>100</span><span>%</span></div>

  <section class="abs legal">
    <h2>IMPORTANT! Please read and sign before completing and submitting.</h2>
    <p>I hereby authorize SENTINEL SHIELD SERVICES to deposit any amounts owed me, as instructed by my employer, by initiating credit entries to my account at the financial institution (hereinafter "Bank") indicated on this form. Further, I authorize Bank to accept and to credit any credit entries indicated by SENTINEL SHIELD SERVICES to my account. In the event that SENTINEL SHIELD SERVICES deposits funds erroneously into my account, I authorize SENTINEL SHIELD SERVICES to debit my account for an amount not to exceed the original amount of the erroneous credit. This authorization is to remain in full force and effect until SENTINEL SHIELD SERVICES and Bank have received written notice from me of its termination in such time and in such manner as to afford SENTINEL SHIELD SERVICES and Bank reasonable opportunity to act on it.</p>
  </section>

  <div class="abs label" style="left:282px;top:834px">Employee Name :</div>
  <div class="abs label" style="left:433px;top:834px">Employee Signature :</div>
  <div class="abs label" style="left:585px;top:834px">Sign Date :</div>
  <div class="abs field tall" style="left:282px;top:850px;width:133px"></div>
  <div class="abs field tall" style="left:433px;top:850px;width:133px"></div>
  <div class="abs field tall" style="left:585px;top:850px;width:134px"></div>

  <div class="abs accept">Accept Document</div>

  <div class="abs section" style="left:282px;top:967px">Only Payroll Manager Signs Below</div>
  <div class="abs label" style="left:281px;top:995px">Company Name :</div>
  <div class="abs label" style="left:432px;top:995px">Comments</div>
  <div class="abs field tall" style="left:281px;top:1011px;width:134px"></div>
  <div class="abs field tall" style="left:433px;top:1011px;width:285px"></div>
  <div class="abs label" style="left:281px;top:1061px">Employee File Number :</div>
  <div class="abs field tall" style="left:281px;top:1077px;width:134px"></div>
</main>

<footer class="abs footer">Copyright © 2016 Company name. All rights reserved.</footer>
</body>
</html>
```